Business Card Design Project

We need a business card for a new technology services company. We develop software and implement software packages for our business customers and although we will begin with just one or two service offerings, our service offerings will expand over time. Our name comes from the an author, KL Barrow, and his "idea" was that opportunity should be based on ability and achievement, not on social status.

We would like to see a design that is standard in its size and shape, but stands apart in its dramatic color contrasts. The card should not use too many colors - the colors used in the background should highlight the brilliant blues of the logo (see attachment) to dramatic effect. The background should not be white.

If necessary, you can change the color of the words "KL Barrow", but not the word "Idea".

Card size should be U.S. standard 2 inches by 3.5 inches and provide for 1/8 inch bleed area on each side.

We need a design for both sides of the business card, one side communicating the company logo and contact information, the other side being purely graphical, incorporating the logo but no other information.

Contact Information Required:
Kate Brook
KateBrook@klbarrowvista.com
614-387-2259

Target Market(s)

Business executives

Industry/Entity Type

Software

Requirements
Must have
• It must have the full company logo on one side, and at least the graphic element of the logo on the other. Either that or the full logo on both.
Nice to have
• It would be nice to have a design that could work without needing two different textures. For example, it would be nice if the entire card could be shiny, not just parts of the card.

It would also be nice if texture is something we could add later.
Should not have
• The card should not use the color green.

```html
<!DOCTYPE html>
<html lang="en">
<head>
<meta charset="utf-8">
<title>KL Barrow Vista – Business Card</title>
<link href="https://fonts.googleapis.com/css2?family=Arimo:wght@400;700&display=swap" rel="stylesheet">
<style>
  :root {
    --stage: #e9e9e9;
    --card-black: #050505;
    --swoosh-grey: #b9bcbf;
    --brand-blue: #1aa0e2;
    --brand-blue-deep: #0a6fae;
    --text-white: #ffffff;
    --card-shadow: rgba(0, 0, 0, 0.28);
  }
  * { box-sizing: border-box; margin: 0; padding: 0; }
  html, body {
    width: 1200px;
    height: 720px;
    overflow: hidden;
    background: var(--stage);
    font-family: "Arimo", Arial, sans-serif;
  }
  .stage {
    position: relative;
    width: 1200px;
    height: 720px;
    display: flex;
    align-items: center;
    justify-content: center;
    gap: 40px;
  }
  .card {
    position: relative;
    width: 540px;
    height: 309px;
    background: var(--card-black);
    border-radius: 4px;
    overflow: hidden;
    box-shadow: 0 10px 24px var(--card-shadow);
  }
  .card__swoosh {
    position: absolute;
    inset: 0;
    width: 100%;
    height: 100%;
  }
  .brand {
    position: absolute;
    display: flex;
    align-items: center;
    gap: 12px;
    color: var(--brand-blue);
    font-weight: 400;
    letter-spacing: -0.5px;
    white-space: nowrap;
  }
  .brand-mark {
    position: absolute;
    display: block;
    border-radius: 50%;
    background: var(--brand-blue);
  }
  /* Front side */
  .card--front .brand {
    left: 34px;
    top: 118px;
    font-size: 30px;
  }
  .card--front .brand-mark {
    left: 250px;
    top: 34px;
    width: 64px;
    height: 64px;
  }
  .holder-name {
    position: absolute;
    left: 50px;
    top: 214px;
    color: var(--brand-blue);
    font-size: 17px;
    font-weight: 700;
    letter-spacing: 1px;
    text-transform: uppercase;
  }
  .contact {
    position: absolute;
    right: 20px;
    top: 138px;
    list-style: none;
    display: flex;
    flex-direction: column;
    align-items: flex-end;
    gap: 16px;
    color: var(--text-white);
    font-size: 12.5px;
  }
  .contact__item {
    display: flex;
    align-items: center;
    gap: 6px;
  }
  .contact__icon { width: 12px; height: 12px; flex: none; }
  /* Back side */
  .card--back .brand {
    left: 34px;
    bottom: 36px;
    font-size: 42px;
  }
  .card--back .brand-mark {
    right: 90px;
    top: 30px;
    width: 140px;
    height: 140px;
  }
</style>
</head>
<body>
<main class="stage">
  <section class="card card--front" aria-label="Card front">
    <svg class="card__swoosh" viewBox="0 0 540 309" preserveAspectRatio="none" aria-hidden="true">
      <defs>
        <linearGradient id="panelBlue" x1="0" y1="1" x2="1" y2="0">
          <stop offset="0" stop-color="#1aa0e2"/>
          <stop offset="1" stop-color="#0a6fae"/>
        </linearGradient>
      </defs>
      <path d="M180 309 C290 240 350 120 392 0 L540 0 L540 309 Z" fill="#b9bcbf"/>
      <path d="M204 309 C312 242 372 124 420 0 L540 0 L540 309 Z" fill="url(#panelBlue)"/>
    </svg>
    <span class="brand-mark" aria-hidden="true"></span>
    <div class="brand">KL Barrow Vista</div>
    <p class="holder-name">Kate Brook</p>
    <ul class="contact">
      <li class="contact__item">
        <svg class="contact__icon" viewBox="0 0 12 12" aria-hidden="true">
          <circle cx="6" cy="6" r="5.4" fill="none" stroke="currentColor" stroke-width="1.1"/>
          <path d="M4 3.2 L5.2 3.2 L5.6 4.8 L4.9 5.4 Q5.6 6.8 6.8 7.3 L7.4 6.6 L8.9 7 L8.9 8.2 Q5.5 8.6 3.8 4.4 Z" fill="currentColor"/>
        </svg>
        <span>614-387-2259</span>
      </li>
      <li class="contact__item">
        <svg class="contact__icon" viewBox="0 0 12 12" aria-hidden="true">
          <rect x="1" y="3" width="10" height="7" fill="none" stroke="currentColor" stroke-width="1.1"/>
          <path d="M1 3 L6 7 L11 3" fill="none" stroke="currentColor" stroke-width="1.1"/>
        </svg>
        <span>KateBrook@klbarrowvista.com</span>
      </li>
    </ul>
  </section>

  <section class="card card--back" aria-label="Card back">
    <span class="brand-mark" aria-hidden="true"></span>
    <div class="brand">KL Barrow Vista</div>
  </section>
</main>
</body>
</html>
```